Im open to ideas.. I was thinking on my business cards aswell as my logo. a place for my name. email. phone number and abn..

ive attched a file with my business logo. which i dont love the colours.. i was think a dark background with charcoal letters so something along those colour schumes but im open to ideas..

BRM Constructions

```html
<!DOCTYPE html>
<html lang="en">
<head>
<meta charset="utf-8">
<title>BRM Constructions – Business Card</title>
<link rel="stylesheet" href="https://fonts.googleapis.com/css2?family=Russo+One&family=Open+Sans:wght@400;600&display=swap">
<style>
  :root {
    --backdrop: #1c1c1c;
    --card: #f7f7f7;
    --ink: #1d1d1d;
    --accent: #d4141c;
    --muted: #555555;
  }
  * { margin: 0; padding: 0; box-sizing: border-box; }
  html, body {
    width: 1200px; height: 873px; overflow: hidden;
    background: var(--backdrop);
  }
  .card {
    position: absolute; left: 100px; top: 152px;
    width: 1000px; height: 570px;
    background: var(--card);
    overflow: hidden;
    font-family: "Open Sans", sans-serif;
  }
  .card-bands { position: absolute; inset: 0; width: 1000px; height: 570px; }
  .brand {
    position: absolute; left: 190px; top: 110px;
    color: var(--ink);
    font-family: "Russo One", sans-serif;
    text-align: center; line-height: 1;
  }
  .brand-name { display: block; font-size: 104px; letter-spacing: 4px; }
  .brand-sub { display: block; font-size: 22px; letter-spacing: 14px; margin-top: 8px; }
  .owner {
    position: absolute; right: 62px; top: 150px; text-align: right;
  }
  .owner-name {
    font-family: "Russo One", sans-serif;
    color: var(--accent); font-size: 28px; letter-spacing: 1px;
  }
  .owner-role { color: var(--muted); font-size: 16px; margin-top: 6px; }
  .owner-web {
    font-family: "Russo One", sans-serif;
    color: var(--accent); font-size: 20px; margin-top: 8px;
  }
  .contact {
    position: absolute; left: 70px; top: 330px;
    color: var(--muted); font-size: 19px;
  }
  .contact-line { display: flex; align-items: center; gap: 10px; margin-bottom: 12px; }
  .contact-line svg { width: 20px; height: 20px; fill: var(--accent); }
  .address {
    font-family: "Russo One", sans-serif;
    color: var(--accent); font-size: 25px; line-height: 1.3; letter-spacing: 1px;
    margin-top: 6px;
  }
  .site-line {
    position: absolute; right: 62px; top: 398px;
    font-family: "Russo One", sans-serif;
    color: var(--accent); font-size: 22px; letter-spacing: .5px;
  }
</style>
</head>
<body>
  <div class="card">
    <svg class="card-bands" viewBox="0 0 1000 570" aria-hidden="true">
      <path d="M0 540 L470 485 L470 570 L0 570 Z" fill="var(--ink)"/>
      <path d="M462 570 Q470 495 540 488 L1000 448 L1000 570 Z" fill="var(--card)"/>
      <path d="M480 570 Q488 508 550 502 L1000 462 L1000 570 Z" fill="var(--accent)"/>
    </svg>

    <div class="brand">
      <span class="brand-name">BRM</span>
      <span class="brand-sub">CONSTRUCTIONS</span>
    </div>

    <div class="owner">
      <div class="owner-name">Daniel Hartwell</div>
      <div class="owner-role">Owner / Founder</div>
      <div class="owner-web">brmconstructions.com</div>
    </div>

    <div class="contact">
      <div class="contact-line">
        <svg viewBox="0 0 24 24"><path d="M3 8c0-2 4-4 9-4s9 2 9 4v2h-5V8H8v2H3z M6 11h12l3 9H3z"/></svg>
        <span>0400555018</span>
      </div>
      <div class="contact-line">
        <svg viewBox="0 0 24 24"><path d="M2 5h20v14H2z M3 6l9 7 9-7" stroke="#f7f7f7" stroke-width="1.5"/></svg>
        <span>info@brmconstructions.com</span>
      </div>
      <div class="address">418 shore 94th st<br>Bayview park ny 11000</div>
    </div>

    <div class="site-line">www.brmconstructions.com</div>
  </div>
</body>
</html>
```